Korvath Supply Website Redesign

Currently korvathsupply.example is focussed on fulfillment and transport from various products in the BBQ segment. However, no we want to update our business activities to Product Development, Brand Development, Online Positioning, Logistics & Aftersales, and Promotional BBQs. We will be a business for Outdoor Leisure Development from A to Z.

Therefore, we need a brand new website. The colours of the current website may be the same. However, i'd like to keep it clean. More white and use blue and green as accent colours. It is a business to business organization so the website should be looking formal and corporate. However we sell fun products so not too formal and corporate.

Pages we need; Home, About, Contact, Our Services (+ page per service) a place to share our news/blogs.

I have added some sort of mock up of an idea. However it needs some finetuning.

Target Market(s)

Businesses

Industry/Entity Type

Corporate/Logistics/Marketing

Coding

Coded - Design and coding required

Colors

Designer to choose colors to be used in the design.

Requirements
Must have
• Show clear distinguishing of the different services we provide (Product Development, Brand Development, Online Positioning, Logistics & Aftersales and Promotional BBQs). Every service should have its own page too. Besides, I would like to have a blog page to share relevant content.
Nice to have
• Show that we are the expert in Outdoor LEisure Development from A to Z
Should not have
• Be too informal. It may be semi-formal

```html
<!DOCTYPE html>
<html lang="en">
<head>
<meta charset="utf-8">
<title>Korvath Supply – Outdoor Leisure Development</title>
<link href="https://fonts.googleapis.com/css2?family=Poppins:wght@600;700;800&family=Roboto:wght@400;500;700&display=swap" rel="stylesheet">
<style>
:root{
  --slate:#345d6b;
  --green:#33a23a;
  --ink:#111;
  --text:#555;
  --footer:#262626;
  --white:#fff;
}
*{box-sizing:border-box;margin:0;padding:0}
html,body{width:1200px;height:2686px;overflow:hidden;background:var(--white);font-family:"Roboto",Arial,sans-serif;color:var(--ink)}
.page{position:relative;width:1200px;height:2686px}
.abs{position:absolute}

/* header */
.site-header{position:absolute;left:0;top:0;width:1200px;height:80px;background:var(--white)}
.brand{position:absolute;left:112px;top:16px;display:flex;align-items:center;gap:10px;font-family:"Poppins",sans-serif;font-weight:800;font-size:38px;color:var(--slate);letter-spacing:1px}
.brand-dot{width:28px;height:28px;border-radius:50%;background:var(--green)}
.main-nav{position:absolute;left:419px;top:32px;display:flex;gap:33px;font-family:"Roboto",sans-serif;font-weight:500;font-size:14.5px;text-transform:uppercase}
.main-nav a{color:var(--ink);text-decoration:none}
.main-nav a.active{color:var(--green)}
.login-btn{position:absolute;left:832px;top:18px;width:138px;height:45px;border-radius:23px;background:var(--slate);color:#fff;font-weight:500;font-size:14px;display:flex;align-items:center;padding-left:21px;gap:8px}
.login-btn .knob{position:absolute;right:8px;top:9px;width:27px;height:27px;border-radius:50%;background:var(--green)}
.social{position:absolute;top:22px;width:37px;height:37px;border:1.5px solid var(--green);border-radius:50%}

/* hero */
.hero{position:absolute;left:0;top:80px;width:1200px;height:600px;background:linear-gradient(180deg,#15204a 0%,#2a2f55 35%,#6b3f2a 70%,#2b1e2a 100%)}
.hero-mark{position:absolute;left:0;top:40px;width:1200px;text-align:center;font-family:"Poppins",sans-serif;font-weight:800;font-size:190px;color:rgba(255,255,255,.25);letter-spacing:4px}
.hero-title{position:absolute;left:0;top:388px;width:1200px;text-align:center;font-family:"Poppins",sans-serif;font-weight:800;font-size:49px;line-height:58px;color:#fff;text-transform:uppercase}

/* services */
.section-title{position:absolute;left:0;width:1200px;text-align:center;font-family:"Poppins",sans-serif;font-weight:800;font-size:34px;color:var(--ink);text-transform:uppercase}
.service{position:absolute;width:272px;height:272px;border-radius:50%;color:#fff;text-align:center}
.service::after{content:"";position:absolute;inset:15px;border:2px solid #fff;border-radius:50%}
.service.slate{background:var(--slate)}
.service.green{background:var(--green)}
.service.featured{width:290px;height:290px;box-shadow:0 14px 30px rgba(0,0,0,.35);background:repeating-linear-gradient(135deg,#345d6b 0 8px,#3d6a6c 8px 16px)}
.service-icon{position:absolute;left:50%;transform:translateX(-50%)}
.service-name{position:absolute;left:0;width:100%;font-family:"Poppins",sans-serif;font-weight:700;font-size:16.5px;line-height:21px;text-transform:uppercase}
.service-text{position:absolute;left:50px;width:190px;font-size:13px;line-height:20px}
.service-arrow{position:absolute;left:50%;transform:translateX(-50%)}

/* difference band */
.difference{position:absolute;left:0;top:1250px;width:1200px;height:343px;background:linear-gradient(90deg,#2f3a4a 0%,#5b4a3a 45%,#7a5030 70%,#3a2e30 100%)}
.difference h2{position:absolute;left:0;top:90px;width:1200px;text-align:center;font-family:"Poppins",sans-serif;font-weight:800;font-size:50px;color:#fff;text-transform:uppercase}
.difference p{position:absolute;left:190px;top:170px;width:820px;text-align:center;font-weight:500;font-size:17px;line-height:26px;color:#fff}

/* insights */
.card{position:absolute;top:1783px;width:317px;height:400px;background:#fff;box-shadow:0 0 8px rgba(0,0,0,.14)}
.card-photo{position:absolute;left:4px;top:4px;width:309px;height:215px}
.card-date{position:absolute;left:4px;top:180px;width:96px;height:39px;background:var(--slate);color:#fff;font-weight:500;font-size:14px;line-height:39px;text-align:center}
.card-title{position:absolute;left:20px;top:243px;font-family:"Roboto",sans-serif;font-weight:700;font-size:14.5px;letter-spacing:.3px;text-transform:uppercase}
.card-rule{position:absolute;left:21px;top:273px;width:34px;height:2px;background:var(--green)}
.card-text{position:absolute;left:21px;top:289px;width:280px;font-size:15px;line-height:21px;color:var(--text)}
.card-link{position:absolute;left:24px;top:358px;font-weight:700;font-size:12.5px;color:var(--green);text-decoration:underline;display:flex;align-items:center;gap:8px}

/* footer */
.site-footer{position:absolute;left:0;top:2286px;width:1200px;height:400px;background:var(--footer);color:#fff}
.footer-col{position:absolute;top:76px}
.footer-col h3{font-weight:700;font-size:14.5px;text-transform:uppercase}
.footer-col h3::after{content:"";display:block;width:52px;height:2px;background:#fff;margin-top:8px}
.footer-col ul{list-style:none;margin-top:20px}
.footer-col li{font-size:15px;line-height:33px;display:flex;align-items:center;gap:14px}
.footer-col li::before{content:"»";font-size:15px}
.footer-brand{position:absolute;left:858px;top:80px;display:flex;align-items:center;gap:10px;font-family:"Poppins",sans-serif;font-weight:800;font-size:36px;letter-spacing:1px}
.footer-brand .brand-dot{background:#fff;width:26px;height:26px}
.footer-address{position:absolute;left:858px;top:152px;display:flex;gap:16px;font-size:15px;line-height:21px}
.contact-bar{position:absolute;left:163px;top:242px;width:874px;height:58px;background:var(--green);display:flex;align-items:center}
.contact-item{display:flex;align-items:center;gap:22px;font-size:15.5px;height:58px}
.contact-ico{width:41px;height:41px;border:1.5px solid #fff;border-radius:50%;display:flex;align-items:center;justify-content:center}
.contact-sep{width:1px;height:38px;background:#fff}
.copyright{position:absolute;left:0;top:348px;width:1200px;text-align:center;font-size:14.5px}
</style>
</head>
<body>
<div class="page">

<header class="site-header">
  <div class="brand"><span class="brand-dot"></span>KORVATH</div>
  <nav class="main-nav">
    <a class="active" href="#">Home</a>
    <a href="#">About Us</a>
    <a href="#">Contact</a>
    <a href="#">Our Services</a>
  </nav>
  <div class="login-btn">LOG IN
    <svg width="11" height="12" viewBox="0 0 11 12"><rect x="1" y="5" width="9" height="7" rx="1" fill="#fff"/><path d="M3 5V3.5a2.5 2.5 0 0 1 5 0V5" stroke="#fff" stroke-width="1.5" fill="none"/></svg>
    <span class="knob"></span>
  </div>
  <span class="social" style="left:1002px"></span>
  <span class="social" style="left:1051px"></span>
</header>

<section class="hero" role="img" aria-label="Night city skyline reflected in water">
  <div class="hero-mark">KORVATH</div>
  <h1 class="hero-title">Outdoor Leisure Development<br>From A to Z</h1>
</section>

<h2 class="section-title" style="top:764px">Our Services</h2>

<div class="service slate" style="left:125px;top:854px">
  <svg class="service-icon" style="top:54px" width="62" height="64" viewBox="0 0 62 64" fill="none" stroke="#fff" stroke-width="4"><circle cx="31" cy="26" r="18"/><path d="M23 46h16M25 54h12"/><circle cx="31" cy="26" r="6" fill="#fff"/></svg>
  <div class="service-name" style="top:150px">Product<br>Development</div>
  <svg class="service-arrow" style="top:204px" width="20" height="20" viewBox="0 0 20 20"><circle cx="10" cy="10" r="10" fill="#fff"/><path d="M8 5l5 5-5 5" stroke="#345d6b" stroke-width="2.5" fill="none"/></svg>
</div>

<div class="service green" style="left:352px;top:854px">
  <svg class="service-icon" style="top:56px" width="66" height="64" viewBox="0 0 66 64" fill="#fff"><rect x="20" y="2" width="32" height="10" rx="2"/><rect x="24" y="15" width="24" height="16"/><path d="M4 56l14-16h24c4 0 4 6 0 6H30h14l16-10c4-2 6 3 3 5L40 58H14l-4 5z"/></svg>
  <div class="service-name" style="top:150px">Brand<br>Development</div>
  <svg class="service-arrow" style="top:204px" width="20" height="20" viewBox="0 0 20 20"><circle cx="10" cy="10" r="10" fill="#fff"/><path d="M8 5l5 5-5 5" stroke="#33a23a" stroke-width="2.5" fill="none"/></svg>
</div>

<div class="service green" style="left:806px;top:854px">
  <svg class="service-icon" style="top:66px" width="86" height="46" viewBox="0 0 86 46" fill="#fff"><rect x="20" y="4" width="38" height="28" rx="3"/><path d="M60 12h14l10 12v8H60z"/><circle cx="34" cy="38" r="7"/><circle cx="70" cy="38" r="7"/><rect x="0" y="8" width="16" height="3"/><rect x="4" y="16" width="12" height="3"/><rect x="8" y="24" width="8" height="3"/></svg>
  <div class="service-name" style="top:150px">Logistics<br>&amp; Aftersales</div>
  <svg class="service-arrow" style="top:204px" width="20" height="20" viewBox="0 0 20 20"><circle cx="10" cy="10" r="10" fill="#fff"/><path d="M8 5l5 5-5 5" stroke="#33a23a" stroke-width="2.5" fill="none"/></svg>
</div>

<div class="service featured" style="left:570px;top:844px">
  <svg class="service-icon" style="top:44px" width="56" height="54" viewBox="0 0 56 54" fill="none" stroke="#fff" stroke-width="3.5"><circle cx="26" cy="30" r="18"/><path d="M8 30h36M26 12c-8 10-8 26 0 36M26 12c8 10 8 26 0 36"/><circle cx="10" cy="10" r="6" fill="#fff"/></svg>
  <div class="service-name" style="top:112px">Online<br>Positioning</div>
  <div class="service-text" style="top:160px">Sed ut perspiciatis unde omnis iste natus error sit voluptatem accusantium dolore</div>
  <svg class="service-arrow" style="top:232px" width="20" height="20" viewBox="0 0 20 20"><circle cx="10" cy="10" r="10" fill="#fff"/><path d="M8 5l5 5-5 5" stroke="#345d6b" stroke-width="2.5" fill="none"/></svg>
</div>

<section class="difference" role="img" aria-label="Cargo port at dusk with container ship, cranes and trucks">
  <h2>We Make the Difference</h2>
  <p>At vero eos et accusamus et iusto odio dignissimos ducimus qui blanditiis praesentium voluptatum deleniti atque corrupti quos dolores et quas molestias excepturi sint occaecati cupiditate non provident, similique sunt in culpa qui officia deserunt mollitia animi, id est laborum et dolorum fuga.</p>
</section>

<h2 class="section-title" style="top:1694px">Latest Insights</h2>

<article class="card" style="left:107px">
  <div class="card-photo" role="img" aria-label="Warehouse worker between shelves of boxes" style="background:linear-gradient(135deg,#8a6a4a,#c9a070 50%,#6e5a44)"></div>
  <div class="card-date">DEC , 2021</div>
  <h3 class="card-title">Lorem ipsum dolor sit amet</h3>
  <div class="card-rule"></div>
  <p class="card-text">Sed ut perspiciatis unde omnis iste natus error sit voluptatem accusantidoloremque laudantium, totam rem aperiam</p>
  <a class="card-link">LEARN MORE <svg width="12" height="12" viewBox="0 0 20 20"><circle cx="10" cy="10" r="9" fill="none" stroke="#33a23a" stroke-width="3"/><path d="M6 10h7M10 6l4 4-4 4" stroke="#33a23a" stroke-width="3" fill="none"/></svg></a>
</article>

<article class="card" style="left:442px">
  <div class="card-photo" role="img" aria-label="Plane over cargo port at sunset" style="background:linear-gradient(180deg,#5a7a9a,#e0a060 55%,#6a4a3a)"></div>
  <div class="card-date">DEC , 2021</div>
  <h3 class="card-title">Lorem ipsum dolor sit amet</h3>
  <div class="card-rule"></div>
  <p class="card-text">Sed ut perspiciatis unde omnis iste natus error sit voluptatem accusantidoloremque laudantium, totam rem aperiam</p>
  <a class="card-link">LEARN MORE <svg width="12" height="12" viewBox="0 0 20 20"><circle cx="10" cy="10" r="9" fill="none" stroke="#33a23a" stroke-width="3"/><path d="M6 10h7M10 6l4 4-4 4" stroke="#33a23a" stroke-width="3" fill="none"/></svg></a>
</article>

<article class="card" style="left:777px">
  <div class="card-photo" role="img" aria-label="Business team meeting in a bright office" style="background:linear-gradient(135deg,#d8dcdc,#9aa0a0 50%,#5a5a5e)"></div>
  <div class="card-date">DEC , 2021</div>
  <h3 class="card-title">Lorem ipsum dolor sit amet</h3>
  <div class="card-rule"></div>
  <p class="card-text">Sed ut perspiciatis unde omnis iste natus error sit voluptatem accusantidoloremque laudantium, totam rem aperiam</p>
  <a class="card-link">LEARN MORE <svg width="12" height="12" viewBox="0 0 20 20"><circle cx="10" cy="10" r="9" fill="none" stroke="#33a23a" stroke-width="3"/><path d="M6 10h7M10 6l4 4-4 4" stroke="#33a23a" stroke-width="3" fill="none"/></svg></a>
</article>

<footer class="site-footer">
  <div class="footer-col" style="left:115px">
    <h3>Quick Links</h3>
    <ul><li>Home</li><li>About Us</li><li>Our Services</li></ul>
  </div>
  <div class="footer-col" style="left:383px">
    <h3>Other Links</h3>
    <ul><li>Terms Of Use</li><li>Privacy Policy</li><li>Contact Us</li></ul>
  </div>
  <div class="footer-col" style="left:652px">
    <h3>Useful Links</h3>
    <ul><li>FAQ</li><li>Team Members</li><li>Help Service</li></ul>
  </div>
  <div class="footer-brand"><span class="brand-dot"></span>KORVATH</div>
  <div class="footer-address">
    <svg width="10" height="14" viewBox="0 0 10 14" style="margin-top:3px"><path d="M5 0a5 5 0 0 1 5 5c0 4-5 9-5 9S0 9 0 5a5 5 0 0 1 5-5z" fill="#fff"/><circle cx="5" cy="5" r="2" fill="#262626"/></svg>
    <span>Marrowgate Lane 12,<br>5521 KT Vellen</span>
  </div>
  <div class="contact-bar">
    <div class="contact-item" style="margin-left:32px">
      <span class="contact-ico"><svg width="18" height="18" viewBox="0 0 24 24"><path d="M6 2l4 4-2 3c1 3 3 5 6 6l3-2 4 4-3 4C9 21 3 15 2 5z" fill="#fff"/></svg></span>+31 (0)10 555 0142
    </div>
    <span class="contact-sep" style="margin-left:28px"></span>
    <div class="contact-item" style="margin-left:40px">
      <span class="contact-ico"><svg width="18" height="18" viewBox="0 0 24 24" fill="none" stroke="#fff" stroke-width="2"><rect x="4" y="8" width="16" height="13" rx="1"/><path d="M8 8V3h8v5M8 13h8M8 17h8"/></svg></span>+31 (0)10 555 0143
    </div>
    <span class="contact-sep" style="margin-left:40px"></span>
    <div class="contact-item" style="margin-left:54px">
      <span class="contact-ico"><svg width="18" height="14" viewBox="0 0 24 18" fill="none" stroke="#fff" stroke-width="2"><rect x="1" y="1" width="22" height="16" rx="2"/><path d="M1 3l11 8 11-8"/></svg></span>info@korvathsupply.example
    </div>
  </div>
  <p class="copyright">© 2021 Korvath Supply. All Rights Reserved</p>
</footer>

</div>
</body>
</html>
```